Business Card Design Project

Business Card design based on logo.
Updates

I need business card, letterhead, envelope, and if possible, Powerpoint slide template.

On front of business card: Just logo- and  my name and title:  Harriet Lindqvist, Principal

On reverse-logo and the rest of the contact info:

4871 Quarry Lane
Davis, CA 95618
650-318-2764
hl@brackenstudyworks.example

On letterhead-Just logo at top, at bottom  the rest-very small along the bottom

On PPT slide-just the logo.

I also want to try a few other colors-I like lime/dark grey (not black) but would like to try Sienna, maybe also indigo or bright blue-green.

I forgot to add-

On the business card-switch to vertical on reverse side and put:

Reverse side-switch to vertical and list:

Harriet Lindqvist
Principal
Bracken Study Works, LLC

650-318-2764

4871 Quarry Lane
Davis, CA 95618

Harriet Lindqvist
Principal

650-318-2764

4871 Quarry Lane
Davis, CA 95618

I have another project at the same time-for Stationery. Feel free to submit to that one also.

That one includes letterhead, envelope, PPT slide, folder cover sheet-HL

Industry/Entity Type

Business

Requirements
Must have
• Must use logo-preferably lime green version-with gray, not black or just 2-tone -logo on colored background.

```html
<!DOCTYPE html>
<html lang="en">
<head>
<meta charset="utf-8">
<title>Bracken Study Works — Business Cards</title>
<link href="https://fonts.googleapis.com/css2?family=Open+Sans:wght@400;600;700&display=swap" rel="stylesheet">
<style>
  :root {
    --lime: #9cba2e;
    --charcoal: #454547;
    --ink: #3a3a3c;
    --paper: #ffffff;
    --backdrop: #1b1b1b;
    --muted: #4a4a4a;
  }
  * { margin: 0; padding: 0; box-sizing: border-box; }
  html, body { width: 1200px; height: 722px; overflow: hidden; }
  body {
    background: var(--backdrop);
    font-family: "Open Sans", Arial, sans-serif;
    position: relative;
  }
  .card {
    position: absolute;
    width: 525px;
    height: 300px;
    border-radius: 14px;
    overflow: hidden;
  }
  .card--front   { left: 62px;  top: 47px;  background: var(--paper); }
  .card--back    { left: 612px; top: 47px;  background: var(--paper); }
  .card--lime    { left: 62px;  top: 376px; background: var(--lime); height: 298px; }
  .card--charcoal{ left: 612px; top: 376px; background: var(--charcoal); height: 298px; }

  .brand {
    position: absolute;
    display: flex;
    align-items: center;
    gap: 9px;
    font-weight: 600;
    letter-spacing: 0.5px;
    white-space: nowrap;
  }
  .brand__square { width: 13px; height: 13px; background: currentColor; flex: none; }

  .card--front .brand { left: 30px; top: 136px; font-size: 19px; color: var(--ink); }

  .divider {
    position: absolute; left: 272px; top: 71px; width: 2px; height: 175px;
    background: linear-gradient(to bottom, rgba(0,0,0,0), #9a9a9a 40%, #9a9a9a 60%, rgba(0,0,0,0));
  }
  .contact {
    position: absolute; left: 288px; right: 14px; top: 70px;
    color: var(--muted); font-size: 12px; white-space: nowrap;
  }
  .contact__name { color: var(--lime); font-weight: 700; font-size: 16px; line-height: 20px; }
  .contact__title { font-size: 13px; margin-top: 1px; }
  .contact__list { list-style: none; margin-top: 18px; }
  .contact__list li { display: flex; align-items: center; gap: 6px; line-height: 18.5px; }
  .contact__list svg { width: 11px; height: 11px; fill: var(--lime); flex: none; }
  .contact__address { margin-top: 13px; line-height: 19px; font-size: 12.5px; }

  .centered { left: 0; right: 0; justify-content: center; }
  .card--back .brand { top: 132px; font-size: 26px; color: var(--ink); }
  .card--lime .brand { top: 160px; font-size: 26px; color: #111111; }
  .card--charcoal .brand { top: 160px; font-size: 30px; color: var(--lime); }

  .web {
    position: absolute; left: 0; right: 0; text-align: center;
    font-size: 12.5px; letter-spacing: 2px;
  }
  .card--back .web { top: 220px; color: var(--ink); }
  .card--lime .web { top: 244px; color: #ffffff; }
  .card--charcoal .web { top: 244px; color: #ffffff; }
  .web__accent { color: var(--lime); }
</style>
</head>
<body>

  <section class="card card--front" aria-label="Card front">
    <div class="brand"><span class="brand__square"></span>Bracken Study Works</div>
    <div class="divider"></div>
    <div class="contact">
      <p class="contact__name">Harriet Lindqvist</p>
      <p class="contact__title">Principal</p>
      <ul class="contact__list">
        <li><svg viewBox="0 0 12 12"><path d="M2.5 1 L4.5 1 L5.2 3.6 L4 4.6 C4.7 6 6 7.3 7.4 8 L8.4 6.8 L11 7.5 L11 9.5 C11 10.4 10.4 11 9.5 11 C5 11 1 7 1 2.5 C1 1.6 1.6 1 2.5 1 Z"/></svg>650-318-2764</li>
        <li><svg viewBox="0 0 12 12"><rect x="3" y="0.5" width="6" height="11" rx="1"/><rect x="4" y="2" width="4" height="6.5" fill="#fff"/></svg>650-318-2764</li>
        <li><svg viewBox="0 0 12 12"><rect x="0.5" y="2.5" width="11" height="7.5" rx="1"/><path d="M1 3 L6 7 L11 3" stroke="#fff" stroke-width="1" fill="none"/></svg>hl@brackenstudyworks.example</li>
        <li><svg viewBox="0 0 12 12"><circle cx="6" cy="6" r="5.3"/><path d="M0.8 6 H11.2 M6 0.8 V11.2 M6 0.8 C3.5 3.5 3.5 8.5 6 11.2 M6 0.8 C8.5 3.5 8.5 8.5 6 11.2" stroke="#fff" stroke-width="0.8" fill="none"/></svg>www.brackenstudyworks.example</li>
      </ul>
      <p class="contact__address">4871 Quarry Lane<br>Davis, CA 95618</p>
    </div>
  </section>

  <section class="card card--back" aria-label="Card back, white">
    <div class="brand centered"><span class="brand__square"></span>Bracken Study Works</div>
    <p class="web">www.<span class="web__accent">brackenstudyworks</span>.example</p>
  </section>

  <section class="card card--lime" aria-label="Card back, lime">
    <div class="brand centered"><span class="brand__square"></span>Bracken Study Works</div>
    <p class="web">www.brackenstudyworks.example</p>
  </section>

  <section class="card card--charcoal" aria-label="Card back, charcoal">
    <div class="brand centered">Bracken Study Works</div>
    <p class="web">www.<span class="web__accent">brackenstudyworks</span>.example</p>
  </section>

</body>
</html>
```